Harborview Estates Business Card for Apartment Buildings

Create business cards for resident managers who run apartment buildings. The audience is the public who are searching for apartment rentals, and current residents who live at the apartment building. Key design element will be incorporating the company logo, however, the logo cannot dominate. The building name and manager name are more important than the logo. Current business card design leaves little room for copy, so we may need to reduce the size on the current card to allow for more space for copy.

Target Market(s)

Adults 18-65 years of age, who are looking for an apartment rental, plus current residents who live at our apartment buildings.

Industry/Entity Type

Property Management

Contact Information for Business Card

A major design element will be use of the company logo. Important property and manager contact information must be part of the design. The size of the logo will need to be reduced to make room for building and manager contact copy.

Font styles to use
Sans Serif

Colors
3176b5
000000
959595
ffffff

Requirements
Must have
• 1) Incorporate the company logo.
• 2) Use the company colors (dark blue, black/grey, over white).
• 3) FEATURE THE BUILDING NAME
• 4) FEATURE THE MANAGER NAME
• 5) The company name is less important than BUILDING and MANAGER
• 6) Manager contact information
• **SEE ATTACHED CREATIVE BRIEF**
Nice to have
• 1) Back of card logo watermark
• 2) Ability to write notes on back of carfd
Should not have
• Avoid letting the company logo dominate the card, the building name and manager are more important than the company logo.

```html
<!DOCTYPE html>
<html lang="en">
<head>
<meta charset="utf-8">
<title>Harborview Estates Business Card</title>
<link rel="stylesheet" href="https://fonts.googleapis.com/css2?family=Roboto:wght@400;500;700&family=Roboto+Condensed:wght@700&display=swap">
<style>
  :root {
    --blue: #1569a8;
    --blue-back: #126bad;
    --plate: #47484b;
    --paper: #f1f1f1;
    --white: #ffffff;
    --backdrop: #2a2a2a;
    --rule: #959595;
  }
  * { margin: 0; padding: 0; box-sizing: border-box; }
  html, body { width: 1200px; height: 960px; overflow: hidden; }
  body { background: var(--backdrop); font-family: "Roboto", Arial, sans-serif; position: relative; }

  .card { position: absolute; width: 600px; height: 340px; overflow: hidden; }
  .card-back { left: 320px; top: 110px; background: var(--blue-back); }

  .card-front { left: 320px; top: 493px; height: 342px; background: var(--paper); }

  .brand { position: absolute; right: 36px; top: 62px; display: flex; align-items: center; gap: 10px; }
  .brand-mark { width: 18px; height: 18px; background: var(--blue); }
  .brand-name { font-size: 21px; font-weight: 700; color: var(--blue); letter-spacing: 0.5px; }

  .name-plate { position: absolute; left: 0; top: 155px; width: 288px; height: 60px; }
  .name-plate svg { position: absolute; inset: 0; }
  .manager-name { position: absolute; left: 29px; top: 7px; font-family: "Roboto Condensed", Arial, sans-serif; font-weight: 700; font-size: 23px; color: var(--white); }
  .manager-title { position: absolute; left: 29px; top: 36px; font-size: 15px; font-weight: 500; color: var(--white); }

  .plate-rule { position: absolute; left: 0; top: 214px; width: 288px; height: 2px; background: var(--rule); }

  .contact-band { position: absolute; left: 0; top: 217px; width: 600px; height: 125px; background: var(--blue); color: var(--white); }
  .contact-list { list-style: none; position: absolute; left: 30px; top: 16px; }
  .contact-list li { display: flex; align-items: center; height: 19px; font-size: 14.5px; }
  .contact-list svg { width: 13px; height: 13px; margin-right: 8px; fill: var(--white); }

  .property { position: absolute; right: 36px; top: 56px; text-align: right; font-size: 14.5px; line-height: 19px; }
  .property-name { font-weight: 700; }
</style>
</head>
<body>
  <div class="card card-back"></div>

  <div class="card card-front">
    <div class="brand">
      <span class="brand-mark"></span>
      <span class="brand-name">HARBORVIEW ESTATES</span>
    </div>

    <div class="name-plate">
      <svg width="288" height="60" viewBox="0 0 288 60"><polygon points="0,0 230,0 288,60 0,60" fill="var(--plate)"/></svg>
      <div class="manager-name">Marisol Duarte</div>
      <div class="manager-title">Resident Manager</div>
    </div>
    <div class="plate-rule"></div>

    <div class="contact-band">
      <ul class="contact-list">
        <li><svg viewBox="0 0 16 16"><path d="M3 1l3 3-1.5 2a9 9 0 0 0 5.5 5.5L12 10l3 3-2 2C7 15 1 9 1 3z"/></svg>555-214-0387</li>
        <li><svg viewBox="0 0 16 16"><path d="M4 0h8v16H4zM5.5 2v10h5V2zM7 13.5h2v1H7z" fill-rule="evenodd"/></svg>555-318-6042</li>
        <li><svg viewBox="0 0 16 16"><path d="M4 1h8v4H4zM1 6h14v6h-3v3H4v-3H1zM5 10v4h6v-4z" fill-rule="evenodd"/></svg>555-402-7719</li>
        <li><svg viewBox="0 0 16 16"><path d="M1 3h14v1L8 9 1 4zM1 6l7 5 7-5v7H1z"/></svg>marisol@harborviewest.com</li>
        <li><svg viewBox="0 0 16 16"><circle cx="8" cy="8" r="7"/><path d="M4 5c2 0 2 2 4 2s1 3 0 4M10 3c0 2 2 2 3 3" stroke="var(--blue)" stroke-width="1.5" fill="none"/></svg>www.harborviewest.com</li>
      </ul>
      <div class="property">
        <div class="property-name">Cedar Bluff Apartments</div>
        <div>2845 Lindell Avenue</div>
        <div>Fairmont, CA 90512</div>
      </div>
    </div>
  </div>
</body>
</html>
```